Business Card Design Project - del varosi group

dear Sirs

we need business card design for our group ( DEL Varosi Group ) , i have got the Logo design of our group from pixel harbor in previous , so all need details relating to our group i think available with you, as well as the the chosen logo design

we hope to provide us with business card logo that to be appropaite and satisfactory to us .

thanks

note : logo design of our group is attached .
Updates

Reason: please extend the deadline of my project for additional 15 days because i didn't received appropriate design for our gruop yet . kindly beaware that i have received 77 design till now , supossed to send me 200-250 design at least . thanks

Target Market(s)

contents

name : Kerem EL Nadiri

position : Operation Manager

Industry/Entity Type

Business

Requirements
Must have

• person name

group logo
Nice to have
• logo color matching with back background

```html
<!DOCTYPE html>
<html lang="en">
<head>
<meta charset="utf-8">
<title>DEL Varosi Group – Business Cards</title>
<link rel="stylesheet" href="https://fonts.googleapis.com/css2?family=Open+Sans:wght@400;600;700&display=swap">
<style>
  :root {
    --backdrop: #b8892a;
    --brand-blue: #1c5a97;
    --deep-blue: #1a3a7a;
    --bright-blue: #2a9ad8;
    --gold: #c9a24a;
    --ink: #1d1d1d;
    --white: #ffffff;
    --icon-blue: #2a7cc4;
  }
  * { margin: 0; padding: 0; box-sizing: border-box; }
  html, body { width: 1200px; height: 686px; overflow: hidden; }
  body {
    background: var(--backdrop);
    font-family: "Open Sans", Arial, sans-serif;
    position: relative;
  }
  .card {
    position: absolute;
    width: 496px;
    height: 282px;
    border-radius: 24px;
    overflow: hidden;
    box-shadow: 2px 3px 4px rgba(0,0,0,0.45);
  }
  .card--front { left: 78px; top: 55px; background: var(--white); }
  .card--back-light { left: 628px; top: 57px; background: var(--white); }
  .card--back-dark {
    left: 327px; top: 369px;
    background: radial-gradient(ellipse at 50% 40%, var(--bright-blue) 0%, #1f6ab8 45%, var(--deep-blue) 100%);
  }
  .card__header {
    height: 62px;
    background: linear-gradient(90deg, var(--deep-blue) 0%, var(--bright-blue) 50%, var(--deep-blue) 100%);
    border-bottom: 3px solid var(--gold);
    display: flex;
    align-items: center;
    justify-content: center;
    color: var(--white);
    gap: 8px;
  }
  .card__name { font-weight: 700; font-size: 15px; }
  .card__divider { width: 1px; height: 14px; background: var(--white); opacity: 0.8; }
  .card__role { font-weight: 700; font-size: 12px; }
  .brand {
    position: absolute;
    left: 0; right: 0;
    display: flex;
    align-items: center;
    justify-content: center;
    gap: 10px;
  }
  .brand__mark { width: 22px; height: 22px; background: var(--gold); }
  .brand__name {
    font-weight: 600;
    font-size: 31px;
    letter-spacing: 0.5px;
    color: var(--brand-blue);
    white-space: nowrap;
  }
  .card--front .brand { top: 114px; }
  .card--back-light .brand { top: 122px; }
  .card--back-dark .brand { top: 124px; }
  .card--back-dark .brand__name { color: var(--white); }
  .contacts {
    position: absolute;
    left: 0; right: 0; top: 202px;
    font-size: 13px;
    color: var(--ink);
    text-align: center;
    line-height: 19px;
  }
  .contacts__row { display: flex; justify-content: center; gap: 16px; }
  .contacts__item { display: inline-flex; align-items: center; gap: 2px; }
  .contacts__item svg { width: 11px; height: 11px; fill: var(--icon-blue); }
</style>
</head>
<body>
  <section class="card card--front">
    <header class="card__header">
      <span class="card__name">Kerem EL Nadiri</span>
      <span class="card__divider"></span>
      <span class="card__role">Operation Manager</span>
    </header>
    <div class="brand">
      <span class="brand__mark"></span>
      <span class="brand__name">DEL VAROSI GROUP</span>
    </div>
    <div class="contacts">
      <div class="contacts__row">
        <span class="contacts__item">
          <svg viewBox="0 0 12 12"><path d="M3 1 L5 3.5 L4 5 Q5 7.5 7 8 L8.5 7 L11 9 L9.5 11 Q4 11 1 3 Z"/></svg>(TF)123-456-7890
        </span>
        <span class="contacts__item">
          <svg viewBox="0 0 12 12"><path d="M3 1 L5 3.5 L4 5 Q5 7.5 7 8 L8.5 7 L11 9 L9.5 11 Q4 11 1 3 Z"/></svg>123-456-7890
        </span>
        <span class="contacts__item">
          <svg viewBox="0 0 12 12"><rect x="3" y="1" width="6" height="4"/><rect x="1" y="5" width="10" height="4" rx="1"/><rect x="3" y="9" width="6" height="2"/></svg>123-456-7890
        </span>
      </div>
      <div class="contacts__row">
        <span class="contacts__item">
          <svg viewBox="0 0 12 12"><path d="M1 3 H11 V10 H1 Z M1 3 L6 7 L11 3" stroke="#fff" stroke-width="0.8"/></svg>name@website.com
        </span>
        <span class="contacts__item">
          <svg viewBox="0 0 12 12"><circle cx="6" cy="6" r="5"/><path d="M1 6 H11 M6 1 V11 M6 1 Q2 6 6 11 M6 1 Q10 6 6 11" stroke="#fff" stroke-width="0.7" fill="none"/></svg>www.website.com
        </span>
      </div>
      <div>Street name City, State, zip code</div>
    </div>
  </section>

  <section class="card card--back-light">
    <div class="brand">
      <span class="brand__mark"></span>
      <span class="brand__name">DEL VAROSI GROUP</span>
    </div>
  </section>

  <section class="card card--back-dark">
    <div class="brand">
      <span class="brand__mark"></span>
      <span class="brand__name">DEL VAROSI GROUP</span>
    </div>
  </section>
</body>
</html>
```